National Mission Critical Construction Contractor needs Stationery Design to make a bold statement

We are a small commercial construction company, working primarily in mission critical facilities across the U.S.. We have exciting corporate changes going an and a new logo and office space so we need new stationery. The final design should incorporate our new logo and invoke a fresh, high-tech feel while looking simple and modern.

Industry/Entity Type

Construction

Contact Information for Business Card

We are required to list our state licensing qualifications on the back of our card.

Font styles to use
Sans Serif

Requirements
Must have
• We need to have a design for second page of stationery, envelopes both standard and with a window and for a 3 x 4 notepad.

```html
<!DOCTYPE html>
<html lang="en">
<head>
<meta charset="utf-8">
<title>Steelbrook Stationery</title>
<link href="https://fonts.googleapis.com/css2?family=Source+Sans+3:wght@400;600&display=swap" rel="stylesheet">
<style>
:root{
  --stage:#a9a8a9;
  --paper:#f5f4f2;
  --white:#ffffff;
  --brand:#1a72c2;
  --accent:#37a6e4;
  --ink:#3a3a3a;
  --faint:#dfe6ee;
}
*{margin:0;padding:0;box-sizing:border-box}
html,body{width:1200px;height:754px;overflow:hidden;background:var(--stage);font-family:"Source Sans 3",sans-serif;color:var(--ink)}
.canvas{position:relative;width:1200px;height:754px}
.sheet{position:absolute;background:var(--paper);box-shadow:0 2px 6px rgba(0,0,0,.25);overflow:hidden}
.brand{display:flex;flex-direction:column;align-items:center;gap:4px;color:var(--brand)}
.brand-dot{border:2px solid var(--brand);border-radius:50%}
.brand-name{font-weight:600;letter-spacing:.04em;line-height:1}
.wave{position:absolute;left:0;bottom:0;display:block}
.decor-ring{position:absolute;border:4px solid var(--faint);border-radius:50%}

/* letterhead */
.letterhead{left:36px;top:32px;width:489px;height:690px}
.letterhead .brand{position:absolute;left:0;right:0;top:28px}
.letterhead .brand-dot{width:36px;height:36px}
.letterhead .brand-name{font-size:15px}
.letterhead .decor-ring{left:62px;top:202px;width:360px;height:360px}
.letter{position:absolute;left:49px;top:193px;width:394px}
.salutation{font-size:13.5px;margin-bottom:22px}
.letter p.body{font-size:7.4px;line-height:11.8px;text-align:justify;margin-bottom:11.8px}
.signoff{position:absolute;left:49px;top:481px;font-size:7.6px;line-height:13px}
.signature{display:block;width:63px;height:26px;margin:5px 0 10px -3px;background:linear-gradient(90deg,#c9c9cc,#e6e6e8);border-radius:3px}
.signoff .who{padding-left:3px}
.letterhead-footer{position:absolute;left:0;right:0;bottom:9px;text-align:center;color:var(--white);font-size:8.4px;line-height:12.5px}
.contact-row{display:flex;justify-content:center;gap:5px;align-items:center}
.contact-row svg{width:7px;height:7px;fill:var(--white)}

/* business cards */
.card-front{left:649px;top:177px;width:214px;height:122px;background:var(--white)}
.card-front .brand{position:absolute;left:10px;top:32px;width:100px}
.card-front .brand-dot{width:22px;height:22px}
.card-front .brand-name{font-size:10px}
.card-divider{position:absolute;left:110px;top:22px;width:1px;height:58px;background:#d6d6d6}
.card-details{position:absolute;left:120px;top:23px;font-size:5.4px;line-height:7.6px;color:#555}
.card-details .name{font-size:8px;font-weight:600;color:var(--brand);line-height:9px}
.card-details .role{color:var(--accent);margin-bottom:5px}
.card-details .gap{margin-bottom:2px}
.card-web{position:absolute;left:0;right:0;bottom:3px;text-align:center;color:var(--white);font-size:5.6px;letter-spacing:.06em}
.card-back{left:894px;top:178px;width:215px;height:122px;background:var(--brand)}
.card-back .brand{position:absolute;left:0;right:0;top:36px;color:var(--white)}
.card-back .brand-dot{width:30px;height:30px;border-color:var(--white)}
.card-back .brand-name{font-size:12px}

/* envelopes */
.envelope-back{left:615px;top:360px;width:549px;height:250px}
.envelope-back .flap{position:absolute;left:0;top:0}
.envelope-back .brand{position:absolute;left:0;right:0;top:24px;color:var(--white)}
.envelope-back .brand-dot{width:33px;height:33px;border-color:var(--white)}
.envelope-back .web{font-size:8.6px;margin-top:5px}
.envelope-front{left:547px;top:471px;width:550px;height:250px}
.envelope-front .brand{position:absolute;left:30px;top:30px;width:110px}
.envelope-front .brand-dot{width:32px;height:32px}
.envelope-front .brand-name{font-size:13px}
.envelope-front .decor-ring{left:306px;top:10px;width:240px;height:240px}
.envelope-front .address{position:absolute;left:0;right:0;bottom:10px;text-align:center;color:var(--white);font-size:8.6px}
</style>
</head>
<body>
<div class="canvas">

  <section class="sheet letterhead">
    <div class="decor-ring"></div>
    <div class="brand">
      <span class="brand-dot"></span>
      <span class="brand-name">STEELBROOK</span>
    </div>
    <div class="letter">
      <p class="salutation">Dear Mr. Hart,</p>
      <p class="body">Lorem ipsum dolor sit amet, consectetur adipiscing elit. Donec orci purus, luctus vitae dignissim eu, iaculis sed purus. Vivamus faucibus, ipsum nec aliquet viverra, leo mauris condimentum ligula, sit amet sagittis enim ligula quis arcu. Nam egestas tortor id nisi porttitor mattis. In tortor ante, ultricies in suscipit a, tempus non massa. Vivamus et auctor mi. Fusce vel massa nulla. Phasellus nec eros mauris, et scelerisque orci.</p>
      <p class="body">Donec malesuada orci vitae nulla accumsan porta a id massa. Quisque accumsan iaculis magna sit amet fringilla. Maecenas consequat, magna eget tincidunt semper, odio nibh rutrum mi, id feugiat ante nisi eu risus. Vestibulum nunc orci, rhoncus a placerat in, ultricies in mi. Cras mattis varius eros, vel fringilla nisi suscipit eget. Quisque scelerisque sagittis nulla at porttitor.</p>
      <p class="body">Sed id augue vitae urna euismod commodo aliquet a quam. Pellentesque arcu velit, cursus et malesuada ut, consequat et diam. Nullam erat sem, rhoncus id ullamcorper vitae, rhoncus et arcu. In ultricies ultricies nulla, ut rutrum nisi iaculis at. Donec eu magna a metus ornare faucibus. Fusce aliquet faucibus ultricies. Morbi semper, est id tincidunt gravida, sem arcu adipiscing lacus, ac bibendum nulla leo eu purus. Quisque nec diam sed risus consectetur a cursus quis nibh. Vestibulum id purus lorem.</p>
      <p class="body">It is a long established fact that a reader will be distracted by the readable content of a page when looking at its layout. The point of using Lorem Ipsum is that it has a more-or-less normal distribution of letters, as opposed to using 'Content here, content here', making it look like readable English. Many desktop publishing packages</p>
    </div>
    <div class="signoff">
      <div>Sincerely,</div>
      <span class="signature" role="img" aria-label="Handwritten signature"></span>
      <div class="who">Daniel Hart</div>
      <div class="who">CEO/ Founder</div>
    </div>
    <svg class="wave" width="489" height="72" viewBox="0 0 489 72">
      <path d="M0 2 Q244 56 489 2" fill="none" stroke="var(--accent)" stroke-width="2"/>
      <path d="M0 6 Q244 60 489 6 L489 72 L0 72 Z" fill="var(--brand)"/>
    </svg>
    <div class="letterhead-footer">
      <div>412 Harbor Way, Juneau, Alaska 99801</div>
      <div class="contact-row">
        <svg viewBox="0 0 10 10"><path d="M2 0 L4 2 L3 4 Q4 6 6 7 L8 6 L10 8 L8 10 Q1 9 0 2 Z"/></svg><span>555 210 4831</span>
        <svg viewBox="0 0 10 10"><rect x="2.5" y="0" width="5" height="10" rx="1"/></svg><span>555 372 9016</span>
        <svg viewBox="0 0 10 10"><rect x="0" y="2" width="10" height="6"/></svg><span>mail@steelbrook.com</span>
        <svg viewBox="0 0 10 10"><circle cx="5" cy="5" r="5"/></svg><span>www.steelbrook.com</span>
      </div>
    </div>
  </section>

  <section class="sheet card-front">
    <div class="brand">
      <span class="brand-dot"></span>
      <span class="brand-name">STEELBROOK</span>
    </div>
    <div class="card-divider"></div>
    <div class="card-details">
      <div class="name">Daniel Hart</div>
      <div class="role">CEO/Founder</div>
      <div>412 Harbor Way</div>
      <div class="gap">Juneau, Alaska 99801</div>
      <div>&#9742; 555 210 4831</div>
      <div>&#9647; 555 372 9016</div>
      <div>&#9993; mail@steelbrook.com</div>
    </div>
    <svg class="wave" width="214" height="30" viewBox="0 0 214 30">
      <path d="M0 2 Q107 22 214 2" fill="none" stroke="var(--accent)" stroke-width="1.5"/>
      <path d="M0 5 Q107 25 214 5 L214 30 L0 30 Z" fill="var(--brand)"/>
    </svg>
    <div class="card-web">www.steelbrook.com</div>
  </section>

  <section class="sheet card-back">
    <div class="brand">
      <span class="brand-dot"></span>
      <span class="brand-name">STEELBROOK</span>
    </div>
  </section>

  <section class="sheet envelope-back">
    <svg class="flap" width="549" height="93" viewBox="0 0 549 93">
      <path d="M0 0 L549 0 L535 60 Q530 93 500 93 L50 93 Q20 93 14 60 Z" fill="var(--brand)"/>
    </svg>
    <div class="brand">
      <span class="brand-dot"></span>
      <span class="web">www.steelbrook.com</span>
    </div>
  </section>

  <section class="sheet envelope-front">
    <div class="decor-ring"></div>
    <div class="brand">
      <span class="brand-dot"></span>
      <span class="brand-name">STEELBROOK</span>
    </div>
    <svg class="wave" width="550" height="58" viewBox="0 0 550 58">
      <path d="M0 2 Q275 52 550 2" fill="none" stroke="var(--accent)" stroke-width="2"/>
      <path d="M0 6 Q275 56 550 6 L550 58 L0 58 Z" fill="var(--brand)"/>
    </svg>
    <div class="address">412 Harbor Way, Juneau, Alaska 99801</div>
  </section>

</div>
</body>
</html>
```